Direct to Consumer extended service contract business with a new disruptive business model needs a

We need a customized wordpress design for a company called 'Bright Harbor Assurance'.
We provide an innovative and unique service contract protection program direct to consumers. This program provides monthly coverage for all electronics purchased in the last 4 years and all electronics the consumer purchases in the future for a low monthly fee. The overall design should communicate a sense of legitimacy, ethics, and superior customer service and support (in an industry that has a huge PR issue to overcome).
Electronics is the first product group, other product groups with different price points to launch in the future..

Target Market(s)

All purchasers of electronic goods...all demographics

Industry/Entity Type

Electronics

Font styles to use
Sans Serif

Requirements
Must have
• Customer Testimonials
Industry News
Customer ratings
Blog posts
Call to action messaging
Like the functional elements and design of quillmesa.example (need to be better)
Nice to have
• Like to see video testimonials
Social network "whats trending related to electronics or service contract industry"
Easy way to register products for warranty

```html
<!DOCTYPE html>
<html lang="en">
<head>
<meta charset="utf-8">
<title>Bright Harbor Assurance</title>
<link rel="stylesheet" href="https://fonts.googleapis.com/css2?family=Source+Sans+3:ital,wght@0,300;0,400;0,600;0,700;1,400;1,600&display=swap">
<style>
:root{
  --green:#1d9a4b;
  --green-dark:#168a40;
  --ink:#333333;
  --muted:#7a7a7a;
  --light:#f3f3f3;
  --bar:#1e1e1e;
  --dark:#232323;
  --darker:#1a1a1a;
  --white:#ffffff;
  --star:#e2543a;
  --star-gold:#e0a13a;
  --link:#26a9e0;
}
*{box-sizing:border-box;margin:0;padding:0}
html,body{width:1200px;height:2568px;overflow:hidden}
body{font-family:"Source Sans 3",sans-serif;color:var(--ink);background:var(--white);position:relative}

/* top bar */
.topbar{height:41px;background:var(--bar);position:relative;color:var(--white);font-size:12px;font-weight:600;letter-spacing:.3px}
.topbar .util{position:absolute;left:130px;top:0;line-height:41px;display:flex;gap:24px}
.topbar .util em{font-style:normal;color:var(--green)}
.topbar .cta{position:absolute;left:938px;width:132px;top:0;height:41px;background:var(--green);text-align:center;line-height:41px}

/* header */
.header{height:103px;position:relative;background:var(--white)}
.brand{position:absolute;left:130px;top:34px;display:flex;align-items:center;gap:12px}
.brand .mark{width:30px;height:30px;background:var(--green)}
.brand .name{font-size:26px;font-weight:700;color:var(--green);letter-spacing:.5px}
.nav{position:absolute;right:130px;top:0;line-height:103px;display:flex;gap:52px;font-size:14px;font-weight:600;color:#666}
.nav .active{color:var(--green)}

/* hero */
.hero{height:698px;background:var(--green);position:relative;color:var(--white)}
.hero h1{position:absolute;left:0;right:0;top:26px;text-align:center;font-weight:300;font-size:46px;line-height:56px}
.hero h1 strong{font-weight:700;display:block}
.hero .sub{position:absolute;left:0;right:0;top:158px;text-align:center;font-size:26px}
.hero .sub b{color:#000;font-weight:700}
.hero-media{position:absolute;left:130px;top:253px;width:520px;height:416px;background:linear-gradient(135deg,#e9ecef 0%,#cfd4d8 55%,#17402a 56%,#0c2a3a 100%);border-radius:6px}
.hero-media .play{position:absolute;left:170px;top:82px}
.hero .quote-title{position:absolute;left:685px;top:270px;font-size:40px;font-weight:400}
.field{position:absolute;left:685px;width:385px;height:52px;border:1.5px solid rgba(255,255,255,.75);border-radius:6px;font-size:17px;line-height:49px;padding-left:18px}
.field svg{position:absolute;right:16px;top:20px}
.btn-quote{position:absolute;left:685px;top:495px;width:385px;height:69px;background:linear-gradient(#2b2b2b,#050505);border-radius:7px;text-align:center;line-height:69px;font-size:28px;font-weight:700}
.hero .arrow{position:absolute;top:321px}

/* protect strip */
.protect{height:82px;background:var(--light);position:relative}
.protect p{position:absolute;left:130px;top:0;line-height:82px;font-size:25px;color:#444}
.protect .select{position:absolute;left:685px;top:19px;width:385px;height:44px;background:var(--white);border:1px solid #dcdcdc;font-size:12px;color:#999;line-height:42px;padding-left:16px}
.protect .select svg{position:absolute;right:14px;top:17px}

/* ratings */
.ratings{height:309px;position:relative;border-bottom:1px solid #e2e2e2}
.section-title{font-size:22px;font-weight:700;color:#666}
.ratings .section-title{position:absolute;left:0;right:0;top:48px;text-align:center}
.rating{position:absolute;top:0;width:260px;margin-left:-130px;height:300px;text-align:center}
.rating .stars{position:absolute;left:45px;top:106px;width:170px;height:34px}
.rating .badge{position:absolute;left:74px;top:101px;display:flex;gap:8px}
.rating .badge span{display:block;height:44px;border-radius:3px}
.rating h3{position:absolute;left:0;right:0;top:160px;font-size:19px;line-height:24px;font-weight:700;color:#333}
.rating p{position:absolute;left:0;right:0;top:194px;font-size:13px;line-height:18px;color:#555}
.rating a{position:absolute;left:0;right:0;top:230px;font-size:12px;font-weight:700;color:var(--green);text-decoration:none}

/* blog */
.blog{height:424px;background:var(--light);position:relative}
.blog .heading{position:absolute;left:0;right:0;top:46px;text-align:center}
.blog .heading svg{vertical-align:middle;margin:0 20px}
.post{position:absolute;top:113px;width:296px}
.post .thumb{height:138px;background:var(--white);padding:6px;border:1px solid #e0e0e0}
.post .thumb div{width:100%;height:100%}
.post h4{margin-top:26px;font-size:12px;font-weight:700;color:var(--green)}
.post p{margin-top:10px;font-size:12px;line-height:20px;color:#999}
.post .meta{margin-top:14px;font-size:11px;font-weight:600;color:#555;display:flex;align-items:center;gap:8px}
.post .meta .date{margin-left:24px}

/* news */
.news{height:452px;position:relative;background:var(--white)}
.col-title{position:absolute;top:50px;font-size:22px;font-weight:700;color:#666;padding-bottom:14px;border-bottom:1px solid #e4e4e4}
.news-item{position:absolute;top:125px;width:235px}
.date-box{position:absolute;left:0;top:0;width:53px;height:55px;background:#555;color:var(--white);text-align:center;font-weight:700;line-height:1}
.date-box b{display:block;font-size:20px;padding-top:7px}
.date-box small{font-size:12px}
.news-item .lead{position:absolute;left:80px;top:2px;font-size:13px;font-style:italic;font-weight:600;color:#555}
.news-item .by{position:absolute;left:80px;top:24px;font-size:11px;font-style:italic;color:#999}
.news-item h4{position:absolute;left:0;top:92px;font-size:12px;font-weight:700;color:var(--green)}
.news-item p{position:absolute;left:0;top:120px;width:235px;font-size:12px;line-height:19px;color:#888}
.btn-more{position:absolute;left:0;top:226px;width:94px;height:40px;background:var(--green);color:var(--white);font-weight:700;font-size:16px;text-align:center;line-height:40px}
.feed{position:absolute;left:721px;width:349px}
.feed .avatar{position:absolute;left:0;top:0;width:64px;height:58px}
.feed .body{position:absolute;left:80px;top:-2px;width:270px;font-size:11px;line-height:16px;color:#333}
.feed .body .who{color:#555}
.feed .body .who span{color:#999}
.feed .body a{color:var(--link);text-decoration:none}
.feed .body .show{color:#999;margin-top:4px}

/* testimonials */
.testimonials{height:349px;background:var(--dark);position:relative;color:var(--white)}
.testimonials h2{position:absolute;left:0;right:0;top:28px;text-align:center;font-size:21px;font-weight:700}
.quote-ring{position:absolute;left:130px;top:76px;width:128px;height:128px;border-radius:50%;border:2px solid #555;background:#2b2b2b}
.photo-ring{position:absolute;left:205px;top:72px;width:136px;height:136px;border-radius:50%;border:2px solid #555;background:radial-gradient(circle at 50% 40%,#8d8a86,#3e3b38);overflow:hidden}
.photo-ring svg{position:absolute;left:50px;top:46px}
.testimonials blockquote{position:absolute;left:373px;top:92px;width:697px;font-size:14px;font-style:italic;line-height:24px;color:#cfcfcf}
.testimonials .author{position:absolute;left:373px;top:176px;font-size:18px;font-weight:700}
.testimonials .author span{color:var(--green)}
.testimonials .chev{position:absolute;top:122px}
.socials{position:absolute;left:0;right:0;top:266px;display:flex;justify-content:center;gap:12px}
.socials span{width:46px;height:46px;border-radius:50%;border:2px solid #555}

/* footer */
.footer{height:110px;background:var(--darker);border-top:1px solid #333;position:relative;color:#ccc}
.footer nav{position:absolute;left:0;right:0;top:28px;text-align:center;font-size:12px;font-weight:600;display:flex;justify-content:center;gap:14px}
.footer p{position:absolute;left:0;right:0;top:64px;text-align:center;font-size:10px;color:#999}
</style>
</head>
<body>

<div class="topbar">
  <div class="util"><span>LOGIN</span><span>SUPPORT</span><span>855-500-<em>HARBOR</em> (4272)</span></div>
  <div class="cta">CALL TO ACTION</div>
</div>

<header class="header">
  <div class="brand"><span class="mark"></span><span class="name">Bright Harbor Assurance</span></div>
  <nav class="nav"><span class="active">HOME</span><span>PLANS</span><span>BENEFITS</span><span>FAQS</span><span>ABOUT US</span></nav>
</header>

<section class="hero">
  <h1>THE DAYS OF BUYING EXPENSIVE<strong>IN-STORE SERVICE PLANS ARE OVER!</strong></h1>
  <p class="sub">Don’t buy anymore <b>IN- STORE</b> Service plans</p>

  <div class="hero-media" role="img" aria-label="Promo video: a laptop and a smartphone showing protection coverage, over 10,000 service professionals">
    <svg class="play" width="180" height="180" viewBox="0 0 180 180"><circle cx="90" cy="90" r="84" fill="rgba(255,255,255,.25)" stroke="#5a5a5a" stroke-width="8"/><path d="M70 48 L132 90 L70 132 Z" fill="#3a3a3a"/></svg>
  </div>

  <svg class="arrow" style="left:26px" width="60" height="60" viewBox="0 0 60 60"><circle cx="30" cy="30" r="27" fill="none" stroke="rgba(255,255,255,.45)" stroke-width="3"/><path d="M36 17 L21 30 L36 43 Z" fill="rgba(255,255,255,.45)"/></svg>
  <svg class="arrow" style="left:1114px" width="60" height="60" viewBox="0 0 60 60"><circle cx="30" cy="30" r="27" fill="none" stroke="rgba(255,255,255,.45)" stroke-width="3"/><path d="M24 17 L39 30 L24 43 Z" fill="rgba(255,255,255,.45)"/></svg>

  <div class="quote-title">GET A QUOTE TODAY!</div>
  <div class="field" style="top:337px">What phone do you have?<svg width="14" height="9" viewBox="0 0 14 9"><path d="M0 0 H14 L7 9 Z" fill="#fff"/></svg></div>
  <div class="field" style="top:419px">Where did you buy it?<svg width="14" height="9" viewBox="0 0 14 9"><path d="M0 0 H14 L7 9 Z" fill="#fff"/></svg></div>
  <div class="btn-quote">GET QUOTE</div>
  <div class="field" style="top:584px">Email This quote optional</div>
</section>

<section class="protect">
  <p>Or do you need to protect something else today?</p>
  <div class="select">Find a protection plan for my<svg width="14" height="9" viewBox="0 0 14 9"><path d="M0 0 H14 L7 9 Z" fill="#555"/></svg></div>
</section>

<section class="ratings">
  <h2 class="section-title">Rated #1 by the people who matter most: Customer ratings</h2>

  <div class="rating" style="left:240px">
    <svg class="stars" viewBox="0 0 170 34" width="170" height="34"><defs><path id="st" d="M17 2 L21.3 12.6 L32.5 13.3 L23.9 20.5 L26.6 31.5 L17 25.5 L7.4 31.5 L10.1 20.5 L1.5 13.3 L12.7 12.6 Z"/><linearGradient id="half1"><stop offset="50%" stop-color="#e2543a"/><stop offset="50%" stop-color="#f2c5bb"/></linearGradient></defs><use href="#st" fill="var(--star)"/><use href="#st" x="34" fill="var(--star)"/><use href="#st" x="68" fill="var(--star)"/><use href="#st" x="102" fill="var(--star)"/><use href="#st" x="136" fill="url(#half1)"/></svg>
    <h3>Pomelo App Market</h3><p>4.5 average on 7000+ reviews</p><a>READ THE REVIEWS ▸</a>
  </div>

  <div class="rating" style="left:488px">
    <svg class="stars" viewBox="0 0 170 34" width="170" height="34"><defs><linearGradient id="half2"><stop offset="50%" stop-color="#e0a13a"/><stop offset="50%" stop-color="#f3dcb2"/></linearGradient></defs><use href="#st" fill="var(--star-gold)"/><use href="#st" x="34" fill="var(--star-gold)"/><use href="#st" x="68" fill="var(--star-gold)"/><use href="#st" x="102" fill="var(--star-gold)"/><use href="#st" x="136" fill="url(#half2)"/></svg>
    <h3>Riverbend Market</h3><p>4.5 average on 7000+ reviews</p><a>READ THE REVIEWS ▸</a>
  </div>

  <div class="rating" style="left:721px">
    <svg class="stars" viewBox="0 0 170 34" width="170" height="34"><use href="#st" fill="var(--star)"/><use href="#st" x="34" fill="var(--star)"/><use href="#st" x="68" fill="var(--star)"/><use href="#st" x="102" fill="var(--star)"/><use href="#st" x="136" fill="var(--star)"/></svg>
    <h3>Searchly</h3><p>4.5 average on 7000+ reviews</p><a>READ THE REVIEWS ▸</a>
  </div>

  <div class="rating" style="left:959px">
    <div class="badge" role="img" aria-label="Trade Standards Council accreditation badge"><span style="width:62px;background:#1a5d8a"></span><span style="width:54px;border:2px solid #1a5d8a;background:#fff"></span></div>
    <h3>Riverbend Market</h3><p>Council accredited with top rating</p><a>READ THE REVIEWS ▸</a>
  </div>
</section>

<section class="blog">
  <div class="heading section-title"><svg width="12" height="18" viewBox="0 0 12 18"><path d="M10 2 L3 9 L10 16" fill="none" stroke="#999" stroke-width="3"/></svg>Blog Posts<svg width="12" height="18" viewBox="0 0 12 18"><path d="M2 2 L9 9 L2 16" fill="none" stroke="#555" stroke-width="3"/></svg></div>

  <article class="post" style="left:130px">
    <div class="thumb"><div role="img" aria-label="Opened smartphone showing its circuit board during repair" style="background:linear-gradient(135deg,#3b3b3b,#5f6b4a 50%,#2a2a2a)"></div></div>
    <h4>LOREM IPSUM DOLOR SIT AMET</h4>
    <p>Consecteturadipisicing elit, sed do eimod cteturadipisicing elit, sed do eiusmod tempor incididunt ut labore et.....</p>
    <div class="meta"><svg width="16" height="16" viewBox="0 0 16 16"><path d="M2 14 L3 10 L11 2 L14 5 L6 13 Z" fill="#444"/></svg>POST BY: LOREM IPSUM<span class="date">23-AUGUST 2014</span></div>
  </article>

  <article class="post" style="left:450px">
    <div class="thumb"><div role="img" aria-label="Technician testing a circuit board with a probe" style="background:linear-gradient(135deg,#c9c2b8,#8f8a7f 55%,#4d5a4e)"></div></div>
    <h4>LOREM IPSUM DOLOR SIT AMET</h4>
    <p>Consecteturadipisicing elit, sed do eimod cteturadipisicing elit, sed do eiusmod tempor incididunt ut labore et.....</p>
    <div class="meta"><svg width="16" height="16" viewBox="0 0 16 16"><path d="M2 14 L3 10 L11 2 L14 5 L6 13 Z" fill="#444"/></svg>POST BY: LOREM IPSUM<span class="date">23-AUGUST 2014</span></div>
  </article>

  <article class="post" style="left:772px">
    <div class="thumb"><div role="img" aria-label="Close-up of capacitors on a green circuit board" style="background:linear-gradient(135deg,#2f4f4a,#6d7d78 50%,#1e3530)"></div></div>
    <h4>LOREM IPSUM DOLOR SIT AMET</h4>
    <p>Consecteturadipisicing elit, sed do eimod cteturadipisicing elit, sed do eiusmod tempor incididunt ut labore et.....</p>
    <div class="meta"><svg width="16" height="16" viewBox="0 0 16 16"><path d="M2 14 L3 10 L11 2 L14 5 L6 13 Z" fill="#444"/></svg>POST BY: LOREM IPSUM<span class="date">23-AUGUST 2014</span></div>
  </article>
</section>

<section class="news">
  <h2 class="col-title" style="left:130px;width:235px">Industry News ▸</h2>
  <h2 class="col-title" style="left:721px;width:349px">Social Network(FB News) ▸</h2>

  <div class="news-item" style="left:130px">
    <div class="date-box"><b>14</b><small>JULY</small></div>
    <div class="lead">Aenean auctor wisi et</div><div class="by">Posted by Admin</div>
    <h4>LOREM IPSUM DOLOR SIT AMET.</h4>
    <p>Lorem ips,consectetur ad um dolor sit amet,consectetur ipisicing elit, sed do eiusmod tempor incididunt ut labore et dolore magna aliqua.</p>
    <div class="btn-more">MORE</div>
  </div>

  <div class="news-item" style="left:416px">
    <div class="date-box"><b>14</b><small>JULY</small></div>
    <div class="lead">Aenean auctor wisi et</div><div class="by">Posted by Admin</div>
    <h4>LOREM IPSUM DOLOR SIT AMET.</h4>
    <p>Lorem ips,consectetur ad um dolor sit amet,consectetur ipisicing elit, sed do eiusmod tempor incididunt ut labore et dolore magna aliqua.</p>
    <div class="btn-more">MORE</div>
  </div>

  <div class="feed" style="top:125px">
    <div class="avatar" role="img" aria-label="Nuvola Mobile profile image" style="background:#111"></div>
    <div class="body"><div class="who">Nuvola Mobile <span>@nuvolamobile</span></div>Don't miss a jump, shot or kick. Up your game by connecting your #GripPadThree to <a>#NuvolaTabTwo</a> pic.social.example/k2Rm8<div class="show">▪ Show Photo</div></div>
  </div>
  <div class="feed" style="top:235px">
    <div class="avatar" role="img" aria-label="Game artwork thumbnail" style="background:linear-gradient(135deg,#1b1b3a,#a02a2a)"></div>
    <div class="body"><div class="who">Nuvola Mobile <span>@nuvolamobile</span></div>Don't miss a jump, shot or kick. Up<a>#NuvolaTabTwo</a> pic.social.example/k2Rm8<div class="show">▪ Show Photo</div></div>
  </div>
  <div class="feed" style="top:334px">
    <div class="avatar" role="img" aria-label="Partner profile image" style="background:#111"></div>
    <div class="body"><div class="who">Nuvola Mobile <span>@nuvolamobile</span></div>Up<a>#NuvolaTabTwo</a>pic.social.example/k2Rm8<div class="show">▪ Show Photo</div></div>
  </div>
</section>

<section class="testimonials">
  <h2>Customer Testimonials</h2>
  <svg class="chev" style="left:80px" width="18" height="30" viewBox="0 0 18 30"><path d="M15 3 L4 15 L15 27" fill="none" stroke="#777" stroke-width="3"/></svg>
  <svg class="chev" style="left:1096px" width="18" height="30" viewBox="0 0 18 30"><path d="M3 3 L14 15 L3 27" fill="none" stroke="#777" stroke-width="3"/></svg>
  <div class="quote-ring"><svg width="128" height="128" viewBox="0 0 128 128" style="position:absolute;left:-2px;top:-2px"><text x="22" y="98" font-family="Source Sans 3, sans-serif" font-size="96" font-weight="700" fill="#1d9a4b">“</text></svg></div>
  <div class="photo-ring" role="img" aria-label="Video testimonial from a customer holding a phone"><svg width="36" height="40" viewBox="0 0 36 40"><path d="M4 2 L34 20 L4 38 Z" fill="#fff"/></svg></div>
  <blockquote>Sed ut perspiciatis unde omnis iste natus error sit voluptatem accusantium doloremque laudantium, totam rem aperiam, eaque ipsa quae ab illo inventore veritatis et quasi architecto beatae vitae dicta sunt explicabo. Nemo enim ipsam voluptatem quia voluptas sit aspernatur aut odit aut fugit, sed quia consequuntur</blockquote>
  <div class="author">Dana Whitlock <span>"The Average U.S. Household has about 40 Electric Gadgets"</span></div>
  <div class="socials" role="img" aria-label="Social network links"><span></span><span></span><span></span><span></span></div>
</section>

<footer class="footer">
  <nav><span>PLANS</span><span>BENEFITS</span><span>FAQS</span><span>ABOUT US</span><span>SUPPORT</span><span>PRIVACY POLICY</span><span>TERMS &amp; CONDITIONS</span><span>CONTACT US</span></nav>
  <p>© 2014 Bright Harbor Assurance. All Rights Reserved.</p>
</footer>

</body>
</html>
```